Business Card for Polygraph business in Africa

Business Card . Polygraph Examiner based in Tanzania, East Africa.
Business Card will be used to disseminate contact information to potential clients.
It should convey that I am a professional specifically in the polygraph field and perform my work with integrity.

I have attached the business card that I'm currently using, which I threw together myself initially. It's not professional enough.

Target Market(s)

Banks, Accounting Firms, Government Ministries, Gas, Oil, & Gemstone Mining Concerns, Wildlife Conservation NGOs, International companies located in East Africa.

Industry/Entity Type

Business

Contact Information for Business Card

Veritrace Kilonga
Miriam Holloway
PO Box 48317
Arusha, Tanzania
+255 612 839 274
miriamholloway@postvale.example

Colors
00a990
f37122
faa54b

Requirements
Must have
• - Veritrace Kilonga (with the word "Polygraph" being more prominent than the word "Tanzania")
• - Forensic Examinations
• - Employment Screening
• - Should contain a logo of the Continental Truthline Society (of which I'm a member)
• - I would like an accent design (such as the polygraph "squiggles" of a cardio tracing or such as that)
• - My contact information (less prominent, but large enough to read legibly). I would also consider putting the contact information on the second side of the card.
Nice to have
• My color suggestions are changeable.
Should not have
• Anything "cutesy" or "cartoonish"

```html
<!DOCTYPE html>
<html lang="en">
<head>
<meta charset="utf-8">
<title>Veritrace Kilonga – Business Card</title>
<link rel="stylesheet" href="https://fonts.googleapis.com/css2?family=Roboto:wght@300;400;700&family=Roboto+Condensed:wght@400;700&display=swap">
<style>
  :root {
    --page: #e8e9ec;
    --card-white: #f7f8fa;
    --brand-blue: #0b4fb3;
    --brand-blue-light: #2a6cd0;
    --strip-grey: #6e6e70;
    --text-white: #ffffff;
    --text-blue: #0b4fb3;
    --text-grey: #7a7f88;
  }
  * { margin: 0; padding: 0; box-sizing: border-box; }
  html, body { width: 1200px; height: 886px; overflow: hidden; background: var(--page); }
  .canvas { position: relative; width: 1200px; height: 886px; }

  .card {
    position: absolute; top: 288px; width: 540px; height: 310px;
    border-radius: 18px; overflow: hidden;
    box-shadow: 0 6px 18px rgba(0,0,0,0.12);
    font-family: "Roboto", sans-serif;
  }
  .card--front { left: 40px; background: var(--card-white); }
  .card--back {
    left: 620px;
    background: linear-gradient(160deg, var(--brand-blue-light) 0%, var(--brand-blue) 55%, #0a47a2 100%);
  }

  /* front */
  .front-blue {
    position: absolute; inset: 0; background: var(--brand-blue);
    clip-path: polygon(0 178px, 540px 146px, 540px 310px, 0 310px);
  }
  .front-strip {
    position: absolute; inset: 0; background: var(--strip-grey);
    clip-path: polygon(282px 272px, 540px 272px, 540px 310px, 262px 310px);
  }
  .front-strip-line {
    position: absolute; inset: 0; background: rgba(255,255,255,0.85);
    clip-path: polygon(283px 267px, 540px 267px, 540px 269px, 282px 269px);
  }
  .wordmark {
    position: absolute; left: 34px; top: 76px;
    font-family: "Roboto Condensed", sans-serif; font-weight: 700;
    font-size: 28px; letter-spacing: 0.5px; color: var(--text-blue);
    display: flex; align-items: center; gap: 10px;
  }
  .wordmark-dot { width: 12px; height: 12px; border-radius: 50%; background: var(--text-blue); }
  .tagline {
    position: absolute; left: 56px; top: 116px;
    font-size: 8.5px; letter-spacing: 0.6px; color: var(--text-grey);
    border-top: 1px solid #b9bec6; padding-top: 3px;
  }
  .society-seal {
    position: absolute; right: 24px; top: 20px; width: 50px; height: 50px;
  }
  .holder {
    position: absolute; right: 30px; top: 170px; text-align: right; color: var(--text-white);
  }
  .holder-name {
    font-family: "Roboto Condensed", sans-serif; font-weight: 700; font-size: 19px; letter-spacing: 0.4px;
  }
  .holder-company { font-weight: 300; font-size: 13px; letter-spacing: 0.6px; margin-top: 2px; }
  .contact {
    position: absolute; left: 28px; top: 196px; color: var(--text-white);
    font-size: 11.5px; line-height: 15px;
  }
  .contact-row { display: flex; align-items: center; gap: 7px; }
  .contact-row svg { width: 10px; height: 10px; flex: none; }
  .website-front {
    position: absolute; left: 292px; top: 284px; color: var(--text-white);
    font-size: 11.5px; letter-spacing: 0.2px;
  }

  /* back */
  .back-sheen {
    position: absolute; inset: 0; background: rgba(255,255,255,0.07);
    clip-path: polygon(150px 0, 230px 0, 120px 310px, 60px 310px);
  }
  .back-brand {
    position: absolute; left: 0; right: 0; top: 128px; text-align: center; color: var(--text-white);
  }
  .back-wordmark {
    font-family: "Roboto Condensed", sans-serif; font-weight: 700; font-size: 26px; letter-spacing: 0.6px;
  }
  .back-website { font-weight: 300; font-size: 12px; letter-spacing: 3.5px; margin-top: 6px; }
</style>
</head>
<body>
<main class="canvas">

  <section class="card card--front" aria-label="Business card front">
    <div class="front-blue"></div>
    <div class="front-strip-line"></div>
    <div class="front-strip"></div>

    <div class="wordmark"><span class="wordmark-dot"></span>VERITRACE KILONGA</div>
    <div class="tagline">FORENSIC EXAMINATIONS &bull; EMPLOYMENT SCREENING</div>

    <svg class="society-seal" viewBox="0 0 50 50" role="img" aria-label="Continental Truthline Society membership badge">
      <circle cx="25" cy="25" r="23" fill="none" stroke="var(--brand-blue)" stroke-width="2"/>
    </svg>

    <div class="holder">
      <div class="holder-name">MIRIAM HOLLOWAY</div>
      <div class="holder-company">VERITRACE KILONGA</div>
    </div>

    <div class="contact">
      <div>PO Box 48317</div>
      <div>Arusha, Tanzania</div>
      <div class="contact-row">
        <svg viewBox="0 0 10 10" aria-hidden="true"><path d="M2 0.5 L3.6 2.6 L2.8 3.6 C3.4 5 4.9 6.5 6.4 7.2 L7.4 6.4 L9.5 8 L8.4 9.5 C4.6 9.2 0.8 5.4 0.5 1.6 Z" fill="#fff"/></svg>
        <span>+255 612 839 274</span>
      </div>
      <div class="contact-row">
        <svg viewBox="0 0 10 10" aria-hidden="true"><rect x="0.5" y="1.5" width="9" height="7" fill="none" stroke="#fff" stroke-width="1"/><path d="M0.5 1.5 L5 5.5 L9.5 1.5" fill="none" stroke="#fff" stroke-width="1"/></svg>
        <span>miriamholloway@postvale.example</span>
      </div>
    </div>

    <div class="website-front">www.miriamholloway.example</div>
  </section>

  <section class="card card--back" aria-label="Business card back">
    <div class="back-sheen"></div>
    <div class="back-brand">
      <div class="back-wordmark">VERITRACE KILONGA</div>
      <div class="back-website">www.miriamholloway.example</div>
    </div>
  </section>

</main>
</body>
</html>
```